U.S. Popcorn company needs business cards

We are a popcorn company that manufactures popcorn and sells it to grocery stores worldwide. Our theme is "Americana" and our logo is U.S. route 66 which is the most famous highway in the U.S.

We would like the design to be simple and to use both sides. On the back side we would like to see just the logo and website. The front would be normal details

Target Market(s)

Wholesalers, grocers and distributors

Industry/Entity Type

Manufacture

Contact Information for Business Card

Business name: Prairie Lantern Popcorn
Phone: +1 555 308 4726
Email: Dale@prairielanternpopcorn.com
website: www.prairielanternpopcorn.com
Tag Line: "Fresh from field to shelf"
Name: Dale Whitcombe
Title: Founder/President

Requirements
Must have
• Either this design should be fun or clean and simple. I will let you show me your thougths.
Nice to have
• Anything that ties in the real Hwy Route 66.
• Colors might need to be red, white and blue incorporated.
Should not have
• Not be too busy.

```html
<!DOCTYPE html>
<html lang="en">
<head>
<meta charset="utf-8">
<title>Prairie Lantern Popcorn – Business Cards</title>
<link rel="stylesheet" href="https://fonts.googleapis.com/css2?family=Mulish:wght@400;700;800&display=swap">
<style>
  :root {
    --navy: #112e63;
    --red: #d42222;
    --white: #ffffff;
    --paper: #f4f4f4;
    --stage: #e6e6e6;
    --type: 'Mulish', sans-serif;
  }
  * { margin: 0; padding: 0; box-sizing: border-box; }
  html, body { width: 1200px; height: 576px; overflow: hidden; }
  body { background: var(--stage); font-family: var(--type); position: relative; }

  .card {
    position: absolute;
    top: 139px;
    width: 484px;
    height: 292px;
    border-radius: 6px;
    overflow: hidden;
  }

  /* Back side */
  .card--back { left: 82px; background: var(--navy); }
  .card--back .brand-name {
    position: absolute; left: 0; right: 0; top: 96px;
    text-align: center; color: var(--white);
    font-weight: 800; font-size: 30px; line-height: 1.12; letter-spacing: .5px;
  }
  .card--back .brand-mark {
    position: absolute; left: 50%; top: 52px; width: 26px; height: 26px;
    margin-left: -13px; border-radius: 50%; background: var(--red);
  }
  .card--back .website {
    position: absolute; left: 0; right: 0; top: 256px;
    display: flex; align-items: center; justify-content: center; gap: 12px;
    color: var(--white); font-weight: 700; font-size: 11.5px; letter-spacing: .3px;
  }
  .card--back .website .rule { width: 42px; height: 2px; background: var(--red); }

  /* Front side */
  .card--front { left: 602px; background: var(--navy); }
  .card--front .shapes { position: absolute; inset: 0; }
  .person { position: absolute; left: 21px; top: 38px; color: var(--white); }
  .person .name { font-weight: 700; font-size: 22px; line-height: 1.25; letter-spacing: .2px; }
  .person .role { font-size: 12px; margin-top: 0; }

  .contact-list {
    position: absolute; left: 21px; top: 180px; list-style: none;
    color: var(--white); font-size: 12.5px;
  }
  .contact-list li { display: flex; align-items: center; gap: 8px; height: 17.5px; }
  .contact-list svg { width: 11px; height: 11px; flex: none; }

  .tagline {
    position: absolute; left: 21px; top: 249px;
    color: var(--white); font-size: 13.5px;
  }

  .card--front .brand {
    position: absolute; left: 303px; width: 150px; top: 106px;
    text-align: center; color: var(--navy);
  }
  .card--front .brand-mark {
    display: block; width: 20px; height: 20px; margin: 0 auto 8px;
    border-radius: 50%; background: var(--red);
  }
  .card--front .brand-name { font-weight: 800; font-size: 20px; line-height: 1.12; }
</style>
</head>
<body>

  <section class="card card--back" aria-label="Business card, back side">
    <span class="brand-mark"></span>
    <p class="brand-name">Prairie Lantern<br>Popcorn</p>
    <p class="website"><span class="rule"></span>www.prairielanternpopcorn.com<span class="rule"></span></p>
  </section>

  <section class="card card--front" aria-label="Business card, front side">
    <svg class="shapes" viewBox="0 0 484 292" preserveAspectRatio="none" aria-hidden="true">
      <rect x="0" y="242" width="300" height="31" fill="var(--red)"/>
      <path d="M294,0 Q200,150 292,292 L300,292 Q226,150 324,0 Z" fill="var(--red)"/>
      <path d="M324,0 Q226,150 300,292 L484,292 L484,0 Z" fill="var(--paper)"/>
    </svg>

    <div class="person">
      <h1 class="name">Dale Whitcombe</h1>
      <p class="role">Founder/President</p>
    </div>

    <ul class="contact-list">
      <li>
        <svg viewBox="0 0 12 12" aria-hidden="true"><path d="M1 4 Q6 0 11 4 L9.5 5.5 L8 4.5 L4 4.5 L2.5 5.5 Z M3 6 H9 L10 11 H2 Z" fill="var(--white)"/></svg>
        +1 555 308 4726
      </li>
      <li>
        <svg viewBox="0 0 12 12" aria-hidden="true"><rect x="0.8" y="2.3" width="10.4" height="7.4" fill="none" stroke="var(--white)" stroke-width="1.2"/><path d="M1 2.6 L6 6.8 L11 2.6" fill="none" stroke="var(--white)" stroke-width="1.2"/></svg>
        Dale@prairielanternpopcorn.com
      </li>
      <li>
        <svg viewBox="0 0 12 12" aria-hidden="true"><circle cx="6" cy="6" r="5" fill="none" stroke="var(--white)" stroke-width="1.1"/><ellipse cx="6" cy="6" rx="2.2" ry="5" fill="none" stroke="var(--white)" stroke-width="1"/><path d="M1 6 H11" stroke="var(--white)" stroke-width="1"/></svg>
        prairielanternpopcorn.com
      </li>
    </ul>

    <p class="tagline">"Fresh from field to shelf"</p>

    <div class="brand">
      <span class="brand-mark"></span>
      <p class="brand-name">Prairie Lantern<br>Popcorn</p>
    </div>
  </section>

</body>
</html>
```